Stationery Design + Business Cards

Stationary (letterhead as A4 210x297mm and Letter 8.5"x11", preferably both master page + 2nd pages)

Also need business cards, standard size 50x88mm, can be vertical or horizontal.

You can use a front/back design for the business cards, or front only.

Looking at the uploaded file (devank, you already have that), I want it to use the first logo on the list (4 colors).

Alternative, try the grayscale version (second file).

I need the following information on the business card (in no particular order, let me know what you come up with): 

Firstname Lastlame 
Title 

Mobile +1 555-204-7391 

VelaMorn, Inc. 
24851 Birchwood Ridge Passage 
Brenton, OH 46099 
Tel. +1 555-368-4172 
Fax +1 555-619-0834 

Web: www.velamorn.example 
Twitter: twitter/VelaMorn or @VelaMorn 
Facebook: facebook.com/VelaMorn 

For letterhead, just the company name, address + phone number & fax number 

If you think the phone/fax or something else should not be on the business cards, or something could be missing, let me know.

```html
<!DOCTYPE html>
<html lang="en">
<head>
<meta charset="utf-8">
<title>VelaMorn Letterhead – First &amp; Second Page</title>
<link href="https://fonts.googleapis.com/css2?family=PT+Sans+Narrow:wght@400;700&family=Source+Sans+3:wght@400&display=swap" rel="stylesheet">
<style>
  :root {
    --backdrop: #e6e7e9;
    --paper: #ffffff;
    --brand-blue: #1f4e9e;
    --brand-orange: #f07d22;
    --footer-ink: #4a4a4a;
    --mark-grey: #9a9a9a;
    --shadow: rgba(0, 0, 0, 0.28);
  }
  * { box-sizing: border-box; margin: 0; padding: 0; }
  html, body {
    width: 1200px;
    height: 1000px;
    overflow: hidden;
  }
  body {
    background: var(--backdrop);
    position: relative;
  }
  .sheet {
    position: absolute;
    top: 140px;
    width: 556px;
    height: 720px;
    background: var(--paper);
    box-shadow: 0 6px 18px var(--shadow);
  }
  .sheet--first { left: 29px; }
  .sheet--second { left: 615px; }

  .brand {
    position: absolute;
    top: 38px;
    left: 26px;
    display: flex;
    align-items: center;
    gap: 8px;
  }
  .brand__dot {
    width: 22px;
    height: 22px;
    border-radius: 50%;
    background: var(--brand-orange);
  }
  .brand__name {
    font-family: "Source Sans 3", sans-serif;
    font-weight: 400;
    font-size: 30px;
    line-height: 1;
    color: var(--brand-blue);
  }

  .sheet-footer {
    position: absolute;
    right: 20px;
    bottom: 14px;
    display: flex;
    align-items: center;
    gap: 10px;
  }
  .sheet-footer__details {
    display: flex;
    align-items: baseline;
    font-family: "PT Sans Narrow", sans-serif;
    font-size: 10px;
    line-height: 1;
    color: var(--footer-ink);
    white-space: nowrap;
  }
  .sheet-footer__company { font-weight: 700; }
  .sheet-footer__sep { padding: 0 5px; }
  .sheet-footer__dot {
    width: 18px;
    height: 18px;
    border-radius: 50%;
    background: var(--brand-orange);
  }
  .sheet--second .sheet-footer__dot { background: var(--mark-grey); }
</style>
</head>
<body>

  <section class="sheet sheet--first" aria-label="Letterhead first page">
    <header class="brand">
      <span class="brand__dot"></span>
      <span class="brand__name">VelaMorn</span>
    </header>
    <footer class="sheet-footer">
      <p class="sheet-footer__details"><span class="sheet-footer__company">VelaMorn, Inc.</span><span class="sheet-footer__sep">|</span><span>24851 Birchwood Ridge Passage, Brenton, OH 46099</span><span class="sheet-footer__sep">|</span><span>T +1 555-368-4172</span><span class="sheet-footer__sep">|</span><span>F +1 555-619-0834</span></p>
      <span class="sheet-footer__dot"></span>
    </footer>
  </section>

  <section class="sheet sheet--second" aria-label="Letterhead second page">
    <footer class="sheet-footer">
      <p class="sheet-footer__details"><span class="sheet-footer__company">VelaMorn, Inc.</span><span class="sheet-footer__sep">|</span><span>24851 Birchwood Ridge Passage, Brenton, OH 46099</span><span class="sheet-footer__sep">|</span><span>T +1 555-368-4172</span><span class="sheet-footer__sep">|</span><span>F +1 555-619-0834</span></p>
      <span class="sheet-footer__dot"></span>
    </footer>
  </section>

</body>
</html>
```